National Sales - Pick Up Truck Dealer

We need a logo design for a new vehicle dealership based in Sydney, Australia. The business name is Coastal Iron Haulers Motor Co. We will be selling American 'trucks/pick up trucks' like KRV, Torvan, Blaxer, Morrow T420, Kenzo Raptors, Morrow T640 and the likes.

These vehicles are a luxury option and we would like the logo to be strong, luxurious and masculine.Colours will be black and red or black and blue with the option of grey and white.

Target Market(s)

Men

Industry/Entity Type

Car Dealer

Contact Information for Business Card

Dennis Harlowe
Managing Director
0412 639 274
den@qelvtrk.com.au

Level 5, Brindle Parkway
17 Pemberly Lane
Baulkham Hills
NSW
Australia
Licence No: MD493152

Back of the card

qelvtrk.com.au

Font styles to use
Sans Serif

Colors

Designer to choose colors to be used in the design.

Requirements
Must have
• The company logo that is in the attachments, you can choose from the three which one you would like to work with. Must have vehicle images ....Please look at the attachments as they show examples of what we like and also provides potential images. If you choose to put an image on the front even if it is just the front of the vehicle can you please use the Black KRV Sorrento. Must have all details from the business card details section front and back
Nice to have
• N/A
Should not have
• No cars or standard trucks, please refer to the attached images to understand the product . Should not have any new logos or branding. No other colours besides what is in the logo you choose.

```html
<!DOCTYPE html>
<html lang="en">
<head>
<meta charset="utf-8">
<title>Coastal Iron Haulers Motor Co – Business Card</title>
<link href="https://fonts.googleapis.com/css2?family=Open+Sans:wght@400;600&family=Oswald:wght@500;600&display=swap" rel="stylesheet">
<style>
  :root {
    --backdrop: #1c1c1e;
    --card-black: #141414;
    --card-white: #eeeeee;
    --brand-red: #c8202f;
    --brand-blue: #2f2f7f;
    --ink: #333333;
    --rule: #9a9a9a;
    --silver: #cfcfcf;
    --white: #ffffff;
  }
  * { box-sizing: border-box; margin: 0; padding: 0; }
  html, body {
    width: 1200px; height: 900px; overflow: hidden;
    background: var(--backdrop);
    font-family: "Open Sans", Arial, sans-serif;
  }
  .stage {
    position: relative; width: 1200px; height: 900px;
    display: flex; align-items: center; justify-content: center; gap: 40px;
  }
  .card {
    position: relative; width: 540px; height: 310px;
    border-radius: 22px; overflow: hidden;
    box-shadow: 0 14px 30px rgba(0,0,0,.5);
  }
  /* Back */
  .card--back { background: var(--card-black); }
  .card--back .brand-name {
    position: absolute; left: 0; right: 0; top: 112px; text-align: center;
    font-family: "Oswald", "Arial Narrow", sans-serif; font-weight: 600;
    font-size: 30px; letter-spacing: 1px; text-transform: uppercase;
    color: var(--silver);
  }
  .card--back .website {
    position: absolute; left: 0; right: 0; bottom: 62px; text-align: center;
    font-family: "Oswald", "Arial Narrow", sans-serif; font-weight: 500;
    font-size: 14px; letter-spacing: 3px; color: var(--white);
  }
  /* Front */
  .card--front { background: var(--card-white); color: var(--ink); }
  .card--front .brand-name {
    position: absolute; right: 34px; top: 44px;
    font-family: "Oswald", "Arial Narrow", sans-serif; font-weight: 600;
    font-size: 22px; letter-spacing: .5px; text-transform: uppercase;
    color: var(--brand-blue);
  }
  .card--front .rule-top {
    position: absolute; left: 250px; right: 34px; top: 90px;
    border-top: 1px solid var(--rule);
  }
  .card--front .address {
    position: absolute; right: 34px; top: 100px; text-align: right;
    font-size: 12px; line-height: 1.5; font-style: normal;
  }
  .card--front .rule-mid {
    position: absolute; left: 30px; right: 270px; top: 158px;
    border-top: 1px solid var(--rule);
  }
  .person { position: absolute; left: 30px; top: 168px; }
  .person-name {
    font-family: "Oswald", "Arial Narrow", sans-serif; font-weight: 500;
    font-size: 19px; text-transform: uppercase; line-height: 1.1;
  }
  .person-name .first { color: var(--brand-red); }
  .person-name .last { color: var(--brand-blue); }
  .person-title { font-size: 13px; margin-top: 2px; }
  .person .rule-short {
    width: 215px; border-top: 1px solid var(--rule); margin: 9px 0 8px;
  }
  .contacts { list-style: none; font-size: 14px; line-height: 1.5; }
  .contacts li { display: flex; align-items: center; gap: 7px; }
  .contacts svg { width: 12px; height: 12px; fill: var(--brand-red); flex: none; }
</style>
</head>
<body>
<main class="stage">
  <section class="card card--back" aria-label="Card back">
    <p class="brand-name">Coastal Iron Haulers Motor Co</p>
    <p class="website">www.qelvtrk.com.au</p>
  </section>

  <section class="card card--front" aria-label="Card front">
    <p class="brand-name">Coastal Iron Haulers Motor Co</p>
    <div class="rule-top"></div>
    <address class="address">
      Level 5, Brindle Parkway<br>
      17 Pemberly Lane<br>
      Baulkham Hills NSW Australia<br>
      Licence No: MD493152
    </address>
    <div class="rule-mid"></div>
    <div class="person">
      <p class="person-name"><span class="first">Dennis</span> <span class="last">Harlowe</span></p>
      <p class="person-title">Managing Director</p>
      <div class="rule-short"></div>
      <ul class="contacts">
        <li><svg viewBox="0 0 12 12" aria-hidden="true"><path d="M1 3.5C1 2 2.5 1 6 1s5 1 5 2.5V5H8.5V3.8h-5V5H1zM2.5 6h7l1.5 5H1z"/></svg>0412 639 274</li>
        <li><svg viewBox="0 0 12 12" aria-hidden="true"><path d="M3.5 0h5a1 1 0 0 1 1 1v10a1 1 0 0 1-1 1h-5a1 1 0 0 1-1-1V1a1 1 0 0 1 1-1zm.5 1.5v7.5h4V1.5zM6 9.8a.7.7 0 1 0 0 1.4.7.7 0 0 0 0-1.4z"/></svg>0412 639 274</li>
        <li><svg viewBox="0 0 12 12" aria-hidden="true"><path d="M0 2.5h12v7H0zm1 .8 5 3.5 5-3.5z"/></svg>den@qelvtrk.com.au</li>
      </ul>
    </div>
  </section>
</main>
</body>
</html>
```